Need a Zine cover designed

I’m looking for someone who can design an eye catching and original zine cover. Incorporating the logo I included below. I’m not 100% sure which logo I want to use on the cover, if it’s possible to see how you incorporate the logos on a sample will make it easier for me to decide. Thank you for your time.
For the second logo I’m unsure how to remove the grey background, but I do not want it included in the zine cover
The title of the zine is:
Marigold Crossing
perspectives of culture, life, & love

```html
<!DOCTYPE html>
<html lang="en">
<head>
<meta charset="utf-8">
<title>Marigold Crossing — Zine Cover</title>
<link href="https://fonts.googleapis.com/css2?family=Bungee&family=Michroma&display=swap" rel="stylesheet">
<style>
  :root {
    --backdrop: #a3a4a7;
    --paper-white: #f4f3f1;
    --kraft: #c9a390;
    --kraft-dark: #b58c78;
    --fold-shadow: rgba(90, 55, 40, 0.35);
    --fold-light: rgba(255, 240, 230, 0.35);
    --title-red: #b9332d;
    --ink-brown: #3b1c15;
  }
  html, body {
    margin: 0;
    padding: 0;
    width: 1162px;
    height: 1200px;
    overflow: hidden;
    background: var(--backdrop);
  }
  .canvas {
    position: relative;
    width: 1162px;
    height: 1200px;
  }
  .zine-cover {
    position: absolute;
    left: 201px;
    top: 60px;
    width: 760px;
    height: 1080px;
    background: var(--paper-white);
    box-shadow: 0 10px 30px rgba(0,0,0,0.18);
    overflow: hidden;
  }
  .cover-paper {
    position: absolute;
    inset: 0;
    width: 760px;
    height: 1080px;
  }
  .brand-name {
    position: absolute;
    left: 150px;
    top: 205px;
    width: 300px;
    margin: 0;
    font-family: "Michroma", sans-serif;
    font-size: 30px;
    line-height: 1.25;
    color: var(--ink-brown);
    letter-spacing: 1px;
  }
  .zine-title {
    position: absolute;
    left: 95px;
    top: 440px;
    width: 600px;
    margin: 0;
    font-family: "Bungee", sans-serif;
    font-weight: 400;
    color: var(--title-red);
    line-height: 0.95;
    text-align: center;
  }
  .zine-title .title-line {
    display: block;
    font-size: 96px;
  }
  .zine-title .title-line--second {
    font-size: 88px;
  }
  .zine-subtitle {
    position: absolute;
    left: 230px;
    top: 905px;
    width: 440px;
    margin: 0;
    font-family: "Michroma", sans-serif;
    color: var(--ink-brown);
    text-align: right;
  }
  .zine-subtitle .sub-small {
    display: block;
    font-size: 19px;
    letter-spacing: 6px;
  }
  .zine-subtitle .sub-large {
    display: block;
    margin-top: 8px;
    font-size: 32px;
    letter-spacing: 12px;
  }
</style>
</head>
<body>
<div class="canvas">
  <div class="zine-cover">
    <svg class="cover-paper" viewBox="0 0 760 1080" aria-hidden="true">
      <defs>
        <radialGradient id="kraftTone" cx="50%" cy="45%" r="70%">
          <stop offset="0%" stop-color="var(--kraft)"/>
          <stop offset="100%" stop-color="var(--kraft-dark)"/>
        </radialGradient>
      </defs>
      <path class="kraft-sheet" fill="url(#kraftTone)"
        d="M50,0 L760,0 L760,520 L748,545 L752,575 L735,600 L740,640 L722,670 L728,710 L712,745 L718,790 L700,830 L708,880 L694,920 L702,970 L688,1020 L696,1080
           L70,1080 L58,1040 L72,1000 L55,960 L66,910 L50,870 L62,820 L48,770 L60,720 L45,680 L58,630 L42,580 L56,530 L40,480 L54,430 L38,380 L52,330 L40,280 L55,230 L42,180 L58,130 L45,80 L60,40 Z"/>
      <g class="fold-lines" stroke-width="2">
        <line x1="40" y1="270" x2="760" y2="270" stroke="var(--fold-shadow)"/>
        <line x1="40" y1="272" x2="760" y2="272" stroke="var(--fold-light)"/>
        <line x1="40" y1="540" x2="740" y2="540" stroke="var(--fold-shadow)"/>
        <line x1="40" y1="542" x2="740" y2="542" stroke="var(--fold-light)"/>
        <line x1="40" y1="810" x2="710" y2="810" stroke="var(--fold-shadow)"/>
        <line x1="40" y1="812" x2="710" y2="812" stroke="var(--fold-light)"/>
        <line x1="400" y1="0" x2="400" y2="1080" stroke="var(--fold-shadow)"/>
        <line x1="402" y1="0" x2="402" y2="1080" stroke="var(--fold-light)"/>
      </g>
    </svg>

    <p class="brand-name">Breezewater Society</p>

    <h1 class="zine-title">
      <span class="title-line">Marigold</span>
      <span class="title-line title-line--second">Crossing</span>
    </h1>

    <p class="zine-subtitle">
      <span class="sub-small">PERSPECTIVES OF LIFE</span>
      <span class="sub-large">CULTURE &amp; LOVE</span>
    </p>
  </div>
</div>
</body>
</html>
```